Business card for Luxury Portable Restroom Trailer company

We are a Luxury Portable Restroom Trailer Company Called FALCRIDGE HIRES. Based in Orange County California. We provide portable restroom trailers for events, such as, Weddings, Concerts, Charity events, Sporting events, Tournaments, Corporate events, ect. We rent and Sell the Luxury restrooms. Our colors are white, grey, and Orange. As you will see in the logo we uploaded.
There are 2 people in the company so the names and titles will change for the 3 people but card will remain the same. Here is the information for each Person: Dwight Penner CFO 555 318-0476
next Person: Leon Marchetti VP 555 318-0476
Next Person: Owen Marchetti CEO 555 318-0476
Information to include on the card: Luxury Restroom Trailers Rental and Sales. Weddings, Concerts, Charity, Sporting and Corp. Events.

```html
<!DOCTYPE html>
<html lang="en">
<head>
<meta charset="utf-8">
<title>Falcridge Hires – Business Card</title>
<link rel="stylesheet" href="https://fonts.googleapis.com/css2?family=Open+Sans:wght@400;600;700;800&display=swap">
<style>
  :root {
    --stage: #232323;
    --orange: #f06a25;
    --peach: #fdeadf;
    --grey: #4a4a4c;
    --ink: #1e1e1e;
    --white: #ffffff;
  }
  * { box-sizing: border-box; margin: 0; padding: 0; }
  html, body {
    width: 1200px; height: 768px; overflow: hidden;
    background: var(--stage);
    font-family: "Open Sans", Arial, sans-serif;
  }
  .canvas {
    position: relative; width: 1200px; height: 768px;
    display: flex; align-items: center; justify-content: center; gap: 40px;
  }
  .card {
    position: relative; width: 540px; height: 309px;
    border-radius: 22px; overflow: hidden;
    background: var(--white);
    border-bottom: 5px solid var(--orange);
  }
  /* Front */
  .card-front__wash {
    position: absolute; inset: 0;
    background: radial-gradient(ellipse 70% 80% at 62% 42%, var(--white) 0 38%, var(--peach) 62%, #fdf1ea 100%);
  }
  .wordmark {
    position: absolute; display: flex; align-items: center; gap: 8px;
    font-weight: 800; color: var(--orange); letter-spacing: 0.02em; white-space: nowrap;
  }
  .wordmark__square { width: 12px; height: 12px; background: var(--orange); flex: none; }
  .card-front .wordmark { left: 50%; top: 50%; transform: translate(-50%, -50%); font-size: 40px; gap: 10px; }
  .card-front .wordmark__square { width: 22px; height: 22px; }

  /* Back */
  .card-back .wordmark { left: 28px; top: 122px; font-size: 19px; }
  .card-back__divider {
    position: absolute; left: 284px; top: 44px; width: 2px; height: 150px; background: var(--ink);
  }
  .contact { position: absolute; left: 306px; top: 50px; color: var(--ink); }
  .contact__name { font-size: 25px; font-weight: 700; line-height: 1.1; white-space: nowrap; }
  .contact__first { color: var(--orange); }
  .contact__last { color: var(--grey); }
  .contact__title { font-size: 14px; font-weight: 600; margin: 2px 0 12px; }
  .contact__list { list-style: none; font-size: 14px; line-height: 1.6; }
  .contact__list li { display: flex; align-items: center; gap: 8px; white-space: nowrap; }
  .contact__icon { width: 12px; height: 12px; flex: none; }
  .services {
    position: absolute; left: 0; right: 0; top: 214px; height: 66px;
    background: var(--orange); color: var(--white);
    font-size: 15px; line-height: 1.45;
    display: flex; flex-direction: column; justify-content: center; align-items: center;
  }
  .services__row { display: flex; align-items: center; gap: 6px; white-space: nowrap; }
  .services__bullet { width: 8px; height: 8px; background: var(--white); display: inline-block; }
</style>
</head>
<body>
<main class="canvas">
  <section class="card card-front" aria-label="Card front">
    <div class="card-front__wash" role="img" aria-label="Faint large brand mark in soft peach behind the name"></div>
    <div class="wordmark"><span class="wordmark__square"></span>FALCRIDGE HIRES</div>
  </section>

  <section class="card card-back" aria-label="Card back">
    <div class="wordmark"><span class="wordmark__square"></span>FALCRIDGE HIRES</div>
    <div class="card-back__divider"></div>
    <div class="contact">
      <p class="contact__name"><span class="contact__first">Dwight</span> <span class="contact__last">Penner</span></p>
      <p class="contact__title">CFO</p>
      <ul class="contact__list">
        <li>
          <svg class="contact__icon" viewBox="0 0 12 12"><path d="M2 1l2 0 1 3-1.5 1a6 6 0 0 0 3.5 3.5L8 7l3 1v2a1 1 0 0 1-1 1A9 9 0 0 1 1 2a1 1 0 0 1 1-1z" fill="var(--orange)"/></svg>
          555 318-0476
        </li>
        <li>
          <svg class="contact__icon" viewBox="0 0 12 12"><rect x="0.5" y="2" width="11" height="8" rx="1" fill="var(--orange)"/><path d="M1 3l5 4 5-4" stroke="#fff" fill="none"/></svg>
          info@falcridgehires.com
        </li>
        <li>
          <svg class="contact__icon" viewBox="0 0 12 12"><circle cx="6" cy="6" r="5" fill="none" stroke="var(--orange)" stroke-width="1.4"/><path d="M1 6h10M6 1c-2.5 3-2.5 7 0 10M6 1c2.5 3 2.5 7 0 10" fill="none" stroke="var(--orange)" stroke-width="1"/></svg>
          www.falcridgehires.com
        </li>
      </ul>
    </div>
    <div class="services">
      <p class="services__row"><span class="services__bullet"></span>Luxury Restroom Trailers Rental and Sales</p>
      <p class="services__row"><span class="services__bullet"></span>Weddings <span class="services__bullet"></span>Concerts <span class="services__bullet"></span>Charity <span class="services__bullet"></span>Sporting and Corp <span class="services__bullet"></span>Events</p>
    </div>
  </section>
</main>
</body>
</html>
```